Property Developer - Simple yet Sophisticated and Sharp Business Card

We are a medium sized property developer involved mainly in townhouse developments and land subdivisions.

The company is looking for a simple, sharp and sophisticated business card that will be given to contractors, land owners, financiers etc and thus will need to look professional.

Property development related graphics and art can be used, however the card is not to be too "busy" or crowded. Our company name is Kestrel Developments which could possibly be incorporated into the graphics or artwork.

Single sided and/or double sided designs will be acceptable.

A Simple, Sophisticated, Sharp design please!

Good Luck !

```html
<!DOCTYPE html>
<html lang="en">
<head>
<meta charset="utf-8">
<title>Kestrel Developments – Business Card</title>
<link rel="stylesheet" href="https://fonts.googleapis.com/css2?family=Jost:wght@700;800&display=swap">
<style>
  :root {
    --backdrop: #ece8e1;
    --card-white: #ffffff;
    --brand-orange: #e0832a;
    --ink-black: #0d0d0d;
    --text-white: #ffffff;
  }
  * { box-sizing: border-box; margin: 0; padding: 0; }
  html, body {
    width: 1200px;
    height: 920px;
    overflow: hidden;
    background: var(--backdrop);
    font-family: "Jost", "Futura", sans-serif;
  }
  .canvas {
    position: relative;
    width: 1200px;
    height: 920px;
  }
  .card {
    position: absolute;
    width: 616px;
    height: 343px;
  }
  .card--front {
    left: 313px;
    top: 92px;
    background: var(--card-white);
  }
  .card--back {
    left: 315px;
    top: 465px;
    background: var(--brand-orange);
  }

  /* Front: name lockup */
  .lockup {
    position: absolute;
    left: 0;
    right: 0;
    top: 62px;
    display: flex;
    flex-direction: column;
    align-items: center;
    color: var(--ink-black);
    font-weight: 800;
  }
  .lockup__row {
    display: flex;
    align-items: center;
    gap: 18px;
  }
  .lockup__square {
    width: 44px;
    height: 44px;
    background: var(--brand-orange);
  }
  .lockup__name {
    font-size: 92px;
    line-height: 1;
    letter-spacing: 2px;
  }
  .lockup__tagline {
    margin-top: 26px;
    font-size: 30px;
    line-height: 1;
    letter-spacing: 9px;
    padding-left: 9px;
  }

  /* Back: frame lines and contact details */
  .frame {
    position: absolute;
    left: 0;
    top: 0;
  }
  .contact {
    position: absolute;
    left: 85px;
    top: 228px;
    list-style: none;
    color: var(--text-white);
    font-weight: 700;
    font-size: 15px;
    line-height: 19.5px;
    letter-spacing: 0.3px;
  }
</style>
</head>
<body>
<main class="canvas">
  <section class="card card--front" aria-label="Business card front">
    <div class="lockup">
      <div class="lockup__row">
        <span class="lockup__square" aria-hidden="true"></span>
        <span class="lockup__name">KESTREL</span>
      </div>
      <span class="lockup__tagline">DEVELOPMENTS</span>
    </div>
  </section>

  <section class="card card--back" aria-label="Business card back">
    <svg class="frame" width="616" height="343" viewBox="0 0 616 343" aria-hidden="true">
      <line x1="69" y1="2" x2="69" y2="315" stroke="#0d0d0d" stroke-width="2.5"/>
      <line x1="68" y1="314" x2="614" y2="314" stroke="#0d0d0d" stroke-width="2.5"/>
    </svg>
    <ul class="contact">
      <li>Phone: (07) 3000 4812</li>
      <li>Fax: (07) 3000 4813</li>
      <li>Email: projects.kestreldev@mailbox.com.au</li>
      <li>Postal: PO Box 2214 Westbrook Ridge QLD 4120</li>
    </ul>
  </section>
</main>
</body>
</html>
```